One of a Kind Clean Business Card

We need to design a new business card template for our company. Our company designs and produced merchandising displays. You can see a sample of what we produce on our site www.qorvanexhibits.net. I have uploaded our logo in vector format, as well as a picture of our current business cards. We want a totally different look. We want simple and clean, looking forward to seeing what people create.
Updates

I would like to update the address for Qorvan Display Group Inc. 518 E Tollmere Ln Arlington Heights, IL 60017 Would also note. No QR codes

Industry/Entity Type

Business

Contact Information for Business Card

Need a 1 sided business card designed.

Font styles to use
Serif

Requirements
Must have
• Easy to view; Clean Design
Nice to have
• Features that promote engineering and creativity
Should not have
• Too much clutter, keep it simple

```html
<!DOCTYPE html>
<html lang="en">
<head>
<meta charset="utf-8">
<title>Qorvan Display Group Inc. – Business Card</title>
<link rel="stylesheet" href="https://fonts.googleapis.com/css2?family=Open+Sans:wght@400;600&display=swap">
<style>
  :root {
    --backdrop: #a0a0a0;
    --card-light: #f7f7f7;
    --card-dark: #231f20;
    --card-dark-tone: #2b2728;
    --ink: #1c1c1c;
    --accent: #8b1a1f;
    --white: #ffffff;
  }
  * { margin: 0; padding: 0; box-sizing: border-box; }
  html, body {
    width: 1200px; height: 900px; overflow: hidden;
    background: var(--backdrop);
    font-family: "Open Sans", Arial, sans-serif;
  }
  .canvas { position: relative; width: 1200px; height: 900px; }

  .card { position: absolute; width: 477px; height: 293px; overflow: hidden; }
  .card-front {
    left: 116px; top: 275px;
    background: var(--card-light);
    border-radius: 0 46px 0 46px;
    color: var(--ink);
  }
  .card-back {
    left: 622px; top: 276px;
    background: var(--card-dark);
    border-radius: 46px 0 46px 0;
    color: var(--white);
  }

  .brand-name { position: absolute; text-align: right; font-weight: 400; line-height: 1; }
  .brand-name .brand-main { display: block; font-size: 40px; letter-spacing: 1px; }
  .brand-name .brand-sub { display: block; font-size: 19px; margin-top: 6px; }
  .card-front .brand-name { right: 30px; top: 44px; color: var(--accent); }

  .holder-row {
    position: absolute; left: 24px; right: 0; top: 159px;
    display: flex; align-items: center; gap: 8px;
  }
  .holder-name {
    flex: none;
    font-size: 18px; line-height: 26px; color: var(--accent); letter-spacing: 0.2px;
  }
  .name-rule { flex: 1; height: 1.5px; background: var(--ink); }

  .address {
    position: absolute; left: 33px; top: 231px;
    font-size: 13px; line-height: 17px; font-style: normal;
  }
  .contact-list {
    position: absolute; right: 24px; top: 198px;
    list-style: none; font-size: 13px; line-height: 17.5px; text-align: right;
  }
  .contact-list li { display: flex; justify-content: flex-end; align-items: center; gap: 3px; }
  .contact-icon { width: 10px; height: 10px; fill: var(--accent); flex: none; }

  .back-texture {
    position: absolute; inset: 0;
    background: linear-gradient(135deg, var(--card-dark-tone), var(--card-dark));
  }
  .card-back .brand-name { left: 114px; top: 104px; text-align: left; color: var(--white); }
  .card-back .brand-main { font-size: 44px; }
  .card-back .brand-sub { font-size: 22px; }
  .back-url {
    position: absolute; left: 0; right: 0; top: 235px;
    text-align: center; font-size: 12.5px; font-weight: 600;
  }
</style>
</head>
<body>
<div class="canvas">

  <section class="card card-front">
    <div class="brand-name">
      <span class="brand-main">Qorvan</span>
      <span class="brand-sub">Display Group Inc.</span>
    </div>

    <div class="holder-row">
      <div class="holder-name">DANA HOLLOWAY</div>
      <div class="name-rule"></div>
    </div>

    <address class="address">
      518 E Tollmere Ln<br>
      Arlington Heights, IL 60017
    </address>

    <ul class="contact-list">
      <li>815-555-0142
        <svg class="contact-icon" viewBox="0 0 10 10"><path d="M1 3.5C1 2 2.5 1.5 5 1.5S9 2 9 3.5L7.5 4 7 3H3L2.5 4ZM2.5 4.5H7.5L9 8.5H1Z"/></svg>
      </li>
      <li>312-555-0176
        <svg class="contact-icon" viewBox="0 0 10 10"><path d="M3 0.5H7A1 1 0 0 1 8 1.5V8.5A1 1 0 0 1 7 9.5H3A1 1 0 0 1 2 8.5V1.5A1 1 0 0 1 3 0.5ZM3 2V7.5H7V2Z"/></svg>
      </li>
      <li>dholloway@qorvanexhibits.net
        <svg class="contact-icon" viewBox="0 0 10 10"><path d="M0.5 2H9.5V8.5H0.5ZM1.3 2.6 5 5.6 8.7 2.6Z"/></svg>
      </li>
      <li>www.qorvanexhibits.net
        <svg class="contact-icon" viewBox="0 0 10 10"><circle cx="5" cy="5" r="4.5"/><path d="M1 5H9M5 1C3 3.5 3 6.5 5 9M5 1C7 3.5 7 6.5 5 9" stroke="#f7f7f7" stroke-width="0.8" fill="none"/></svg>
      </li>
    </ul>
  </section>

  <section class="card card-back">
    <div class="back-texture" role="img" aria-label="Faint repeating company name texture across the dark card"></div>
    <div class="brand-name">
      <span class="brand-main">Qorvan</span>
      <span class="brand-sub">Display Group Inc.</span>
    </div>
    <div class="back-url">www.qorvanexhibits.net</div>
  </section>

</div>
</body>
</html>
```